sydney wedding photography business needs a business card design

we need a business card design for a sydney based wedding photography and videography business. our business name is :golden hour studio and film. our target clients are 24-35 yrs female. our style is candid, organic, natural, dynamic. we are a team of young photographers and videographers, and help brides to create memories that they will cherish for the rest of their lives. the logo will be provided. we want an elegant design that reflects our style, and also want to give a great impression to our clients that we are one of the best studios in sydney and our brand means quality and premium service.

Target Market(s)

bride to be, 24-35 years old, living in sydney and surrunding areas

Industry/Entity Type

Wedding Photography

Contact Information for Business Card

address: 57 tarrant street, glenmore nsw 2047
mobile: 0431872259
phone: (02) 9163 2408
info@tidewillowstudio.net.au
www.tidewillowstudio.net.au
facebook:tidewillowweddings
instagram:tidewillowweddings

Font styles to use
Serif
Sans Serif

Requirements
Nice to have
• maybe add my slogan"memories beyond eternity" if the layout looks good
Should not have
• no black color, not good idea for wedding biz card

```html
<!DOCTYPE html>
<html lang="en">
<head>
<meta charset="utf-8">
<title>Golden Hour Studio and Film – Business Card</title>
<link href="https://fonts.googleapis.com/css2?family=Montserrat:wght@500;600;700&display=swap" rel="stylesheet">
<style>
  :root {
    --stage: #4a4847;
    --card: #3d2d26;
    --gold: #e3a51a;
    --ink: #3d2d26;
  }
  * { margin: 0; padding: 0; box-sizing: border-box; }
  html, body {
    width: 1200px;
    height: 1189px;
    overflow: hidden;
    background: var(--stage);
    font-family: "Montserrat", sans-serif;
  }
  .canvas {
    position: relative;
    width: 1200px;
    height: 1189px;
  }
  .card {
    position: absolute;
    width: 640px;
    height: 366px;
    background: var(--card);
    border-radius: 22px;
    box-shadow: 0 18px 40px rgba(0,0,0,.35);
  }
  .card--front { left: 80px; top: 110px; }
  .card--back  { left: 480px; top: 620px; }

  .brand {
    position: absolute;
    left: 0; right: 0;
    text-align: center;
    color: var(--gold);
    font-weight: 700;
    font-size: 34px;
    line-height: 1;
    letter-spacing: 0.5px;
  }
  .card--front .brand { top: 166px; }
  .card--back .brand  { top: 46px; }

  .details {
    position: absolute;
    left: 0; right: 0;
    top: 118px;
    bottom: 24px;
    display: flex;
    justify-content: center;
    align-items: center;
    gap: 24px;
  }
  .person { text-align: right; color: var(--gold); }
  .person__name {
    font-weight: 700;
    font-size: 22px;
    letter-spacing: 0.5px;
    text-transform: uppercase;
    line-height: 1.1;
  }
  .person__role {
    font-weight: 500;
    font-size: 16px;
    line-height: 1.3;
  }
  .divider {
    width: 2px;
    height: 190px;
    background: var(--gold);
  }
  .contact { list-style: none; }
  .contact__item {
    display: flex;
    align-items: center;
    gap: 10px;
    color: var(--gold);
    font-weight: 500;
    font-size: 14px;
    line-height: 1;
    margin: 7px 0;
    white-space: nowrap;
  }
  .contact__icon {
    width: 22px;
    height: 22px;
    border-radius: 5px;
    background: var(--gold);
    display: flex;
    align-items: center;
    justify-content: center;
    flex: none;
  }
  .contact__icon svg { width: 14px; height: 14px; }
</style>
</head>
<body>
<main class="canvas">

  <section class="card card--front" aria-label="Card front">
    <p class="brand">Golden Hour Studio and Film</p>
  </section>

  <section class="card card--back" aria-label="Card back">
    <p class="brand">Golden Hour Studio and Film</p>
    <div class="details">
      <div class="person">
        <p class="person__name">Mara Ellison</p>
        <p class="person__role">Manager</p>
      </div>
      <span class="divider"></span>
      <ul class="contact">
        <li class="contact__item">
          <span class="contact__icon">
            <svg viewBox="0 0 16 16"><rect x="4.5" y="1.5" width="7" height="13" rx="1.5" fill="none" stroke="var(--ink)" stroke-width="1.4"/><circle cx="8" cy="12" r="0.9" fill="var(--ink)"/></svg>
          </span>
          0431 872 259
        </li>
        <li class="contact__item">
          <span class="contact__icon">
            <svg viewBox="0 0 16 16"><path d="M4 2l2.2 2.6-1.2 1.6c.9 1.9 2.3 3.3 4.2 4.2l1.6-1.2L13.4 12l-1.4 1.8C7 13.5 2.5 9 2.2 3.4z" fill="var(--ink)"/></svg>
          </span>
          (02) 9163 2408
        </li>
        <li class="contact__item">
          <span class="contact__icon">
            <svg viewBox="0 0 16 16"><rect x="2" y="4" width="12" height="8.5" fill="none" stroke="var(--ink)" stroke-width="1.4"/><path d="M2 4l6 5 6-5" fill="none" stroke="var(--ink)" stroke-width="1.4"/></svg>
          </span>
          info@tidewillowstudio.net.au
        </li>
        <li class="contact__item">
          <span class="contact__icon">
            <svg viewBox="0 0 16 16" fill="none" stroke="var(--ink)" stroke-width="1.2"><circle cx="8" cy="8" r="6"/><ellipse cx="8" cy="8" rx="2.6" ry="6"/><path d="M2 8h12M3 5h10M3 11h10"/></svg>
          </span>
          www.tidewillowstudio.net.au
        </li>
        <li class="contact__item">
          <span class="contact__icon">
            <svg viewBox="0 0 16 16"><path d="M8 1.5a4.5 4.5 0 0 0-4.5 4.5c0 3.4 4.5 8.5 4.5 8.5s4.5-5.1 4.5-8.5A4.5 4.5 0 0 0 8 1.5z" fill="var(--ink)"/><circle cx="8" cy="6" r="1.7" fill="var(--gold)"/></svg>
          </span>
          57 Tarrant Street, Glenmore NSW 2047
        </li>
        <li class="contact__item">
          <span class="contact__icon">
            <svg viewBox="0 0 16 16" fill="var(--ink)"><circle cx="4" cy="8" r="2"/><circle cx="12" cy="4" r="2"/><circle cx="12" cy="12" r="2"/><path d="M4 8l8-4M4 8l8 4" stroke="var(--ink)" stroke-width="1.3"/></svg>
          </span>
          tidewillowweddings
        </li>
      </ul>
    </div>
  </section>

</main>
</body>
</html>
```